Meridale Nutrition needs Stationary and a business card

We would like to use our current logo. The text can be moved around as needed. The stationary needs to be a 'first page' where the logo is more prominent to be impressive on higher quality paper and a second page where the logo is more subtle where there will be much more information on the page. There are 2 clinic locations which will need include name, address, phone number, fax number, web address. The business card should be single sided and contain this information also.
The design must be contemporary and sophisticated as this is a science based diet run out of a medical clinic.

Target Market(s)

People wanting to lose weight, athletes looking to optimise performance, people with arthritis or fighting cancer

Industry/Entity Type

Business

Contact Information for Business Card

must use the logo. I have attached an example card with the practice details on it. there must be space for the doctors name. Also the website www.meridalenutrition.com.au

Requirements
Must have
• the logo, the business adresses and phone numbers, the website, the doctors name and qualifications
Nice to have
• some creativity
Should not have
• Do not simply reproduce the existing card please

```html
<!DOCTYPE html>
<html lang="en">
<head>
<meta charset="utf-8">
<title>Meridale Nutrition – Business Card</title>
<link rel="stylesheet" href="https://fonts.googleapis.com/css2?family=Open+Sans:wght@400;600;700&display=swap">
<style>
  :root {
    --navy: #2d5d92;
    --deep: #1f4f86;
    --cyan: #1fc0ec;
    --sky: #3aa7d6;
    --ink: #4a5a6a;
    --paper: #ffffff;
    --backdrop: #e9ecef;
    --faint: #eef4f9;
  }
  * { margin: 0; padding: 0; box-sizing: border-box; }
  html, body { width: 1200px; height: 950px; overflow: hidden; }
  body {
    background: var(--backdrop);
    font-family: "Open Sans", sans-serif;
    color: var(--ink);
  }
  .business-card {
    position: absolute;
    left: 160px; top: 215px;
    width: 880px; height: 520px;
    background: var(--paper);
    overflow: hidden;
    box-shadow: 0 10px 30px rgba(20, 40, 70, 0.18);
  }
  .card-watermark {
    position: absolute;
    left: -120px; top: 120px;
    width: 420px; height: 420px;
    border-radius: 50%;
    background: var(--faint);
  }
  .edge-band {
    position: absolute;
    right: 0; top: 0;
    width: 16px; height: 100%;
    background: var(--deep);
  }
  .edge-band::before {
    content: "";
    position: absolute;
    left: 0; top: 0;
    width: 100%; height: 190px;
    background: var(--cyan);
  }
  .base-band {
    position: absolute;
    left: 0; bottom: 0;
    width: 100%; height: 14px;
    background: var(--deep);
  }
  .brand {
    position: absolute;
    left: 440px; top: 50px;
    width: 400px;
    display: flex; align-items: center; gap: 18px;
  }
  .brand-mark {
    flex: 0 0 84px;
    width: 84px; height: 84px;
    border-radius: 50%;
    background: var(--sky);
  }
  .brand-text { min-width: 0; }
  .brand-name {
    font-weight: 700;
    font-size: 27px;
    line-height: 1.15;
    color: var(--navy);
    white-space: nowrap;
  }
  .brand-web {
    margin-top: 4px;
    font-size: 15px;
    color: var(--sky);
    white-space: nowrap;
  }
  .brand-rule {
    position: absolute;
    left: 440px; top: 168px;
    width: 400px; height: 2px;
    background: var(--navy);
  }
  .doctor {
    position: absolute;
    left: 60px; top: 262px;
    width: 760px;
  }
  .doctor-name {
    font-size: 40px;
    font-weight: 600;
    color: var(--navy);
    line-height: 1.1;
  }
  .doctor-credentials {
    margin-top: 6px;
    font-size: 17px;
    color: var(--sky);
    padding-bottom: 12px;
    border-bottom: 2px solid var(--navy);
  }
  .details {
    position: absolute;
    left: 60px; top: 368px;
    display: flex; gap: 64px;
  }
  .detail-block { font-size: 18px; line-height: 1.45; }
  .detail-title { font-weight: 700; color: var(--navy); }
  .detail-tel { font-weight: 700; color: var(--navy); }
  .detail-tel span { font-weight: 400; color: var(--ink); }
</style>
</head>
<body>
  <main class="business-card">
    <div class="card-watermark" role="img" aria-label="Faint circular brand backdrop"></div>

    <div class="brand">
      <div class="brand-mark"></div>
      <div class="brand-text">
        <div class="brand-name">Meridale Nutrition</div>
        <div class="brand-web">www.meridalenutrition.com.au</div>
      </div>
    </div>
    <div class="brand-rule"></div>

    <section class="doctor">
      <h1 class="doctor-name">Dr Elias Marlow</h1>
      <p class="doctor-credentials">MBBS (NSW) MBiomedE FRACS (Ortho) FAOrthA Orthopaedic Surgeon</p>
    </section>

    <section class="details">
      <div class="detail-block">
        <p class="detail-title">Linden</p>
        <p>22-24 Harwell Road</p>
        <p>Linden NSW 2140</p>
        <p class="detail-tel">Tel: <span>02 9000 1482</span></p>
      </div>
      <div class="detail-block">
        <p class="detail-title">Ashby</p>
        <p>118 Calder Street</p>
        <p>Ashby NSW 2035</p>
        <p class="detail-tel">Tel: <span>02 9000 2517</span></p>
      </div>
      <div class="detail-block">
        <p class="detail-title">Shoulder and Elbow</p>
        <p>www.marlowortho.com.au</p>
        <p class="detail-title">Knee surgery</p>
        <p>www.jointclinic.com.au</p>
      </div>
    </section>

    <div class="edge-band"></div>
    <div class="base-band"></div>
  </main>
</body>
</html>
```